Tidewood Builders Business Card Design

We need a business card for an established builder of high quality bespoke homes in Auckland and Northland. We build and renovate homes collaboratively facilitating effective communication between owners, builders, architects, suppliers and tradespeople. We have never built or renovated a home that leaks or has faults. We only use reliable materials. We have never been sued or had legal action taken against us. We are honest builders of bespoke homes not group mass produced homes. Our niche market is in character homes. We practice sustainability and have built a lot of coastal property. We have been in business for over thirty years . We would like to see natural colors of the environment sand,sea and maybe vegetation . The design should communicate quality, sustainability,fair pricing, open communication and the originality of bespoke building. And the fact that the builder is registered.

Industry/Entity Type

Business

Contact Information for Business Card

Rowan Tellick Builders
Ph. 021583917
18 Kestrel Rd Harwood Bay Auckland 0814
PO Box 927 Mangawhai 0583

```html
<!DOCTYPE html>
<html lang="en">
<head>
<meta charset="utf-8">
<title>Tidewood Builders – Business Card</title>
<link rel="stylesheet" href="https://fonts.googleapis.com/css2?family=Anton&family=Open+Sans:wght@400;600&display=swap">
<style>
  :root {
    --backdrop: #ecebe8;
    --card-white: #ffffff;
    --brand-red: #b30000;
    --brand-grey: #4a4a4c;
    --text-light: #ffffff;
    --card-shadow: 0 10px 28px rgba(0,0,0,0.18);
  }
  * { box-sizing: border-box; margin: 0; padding: 0; }
  html, body {
    width: 1200px; height: 900px; overflow: hidden;
    background: var(--backdrop);
  }
  .canvas {
    position: relative; width: 1200px; height: 900px;
    display: flex; align-items: center; justify-content: center; gap: 40px;
  }
  .card {
    position: relative; width: 540px; height: 309px;
    background: var(--card-white);
    box-shadow: var(--card-shadow);
    overflow: hidden;
  }
  .wordmark {
    display: flex; align-items: center; gap: 10px;
    font-family: "Anton", "Impact", sans-serif;
    font-weight: 400; color: var(--brand-grey);
    letter-spacing: 0.5px; white-space: nowrap;
  }
  .wordmark__square {
    display: block; background: var(--brand-red);
  }
  /* Front face */
  .card--front .wordmark {
    position: absolute; left: 50%; top: 50%;
    transform: translate(-50%, -50%);
    font-size: 44px;
  }
  .card--front .wordmark__square { width: 16px; height: 16px; }
  /* Back face */
  .card__band {
    position: absolute; inset: 0; width: 100%; height: 100%;
  }
  .card__band polygon { fill: var(--brand-red); }
  .address {
    position: absolute; left: 36px; top: 58px;
    font-family: "Open Sans", sans-serif; font-size: 14px; line-height: 21px;
    color: var(--text-light);
  }
  .contact {
    position: absolute; right: 30px; top: 26px; text-align: right;
    font-family: "Open Sans", sans-serif; color: var(--text-light);
  }
  .contact__name { font-size: 15px; font-weight: 600; }
  .contact__phone {
    display: inline-flex; align-items: center; gap: 5px;
    font-size: 11px; margin-top: 4px;
  }
  .contact__phone svg { width: 11px; height: 11px; fill: var(--text-light); }
  .card--back .wordmark {
    position: absolute; right: 34px; bottom: 34px;
    font-size: 42px;
  }
  .card--back .wordmark__square { width: 15px; height: 15px; }
</style>
</head>
<body>
<main class="canvas">
  <section class="card card--front" aria-label="Card front">
    <div class="wordmark"><span class="wordmark__square"></span>Tidewood Builders</div>
  </section>

  <section class="card card--back" aria-label="Card back">
    <svg class="card__band" viewBox="0 0 540 309" preserveAspectRatio="none" aria-hidden="true">
      <polygon points="0,0 540,0 540,150 0,285"/>
    </svg>
    <address class="address" style="font-style:normal">
      18 Kestrel Rd Harwood Bay<br>
      Auckland 0814 PO Box 927<br>
      Mangawhai 0583
    </address>
    <div class="contact">
      <div class="contact__name">Rowan Tellick Builders</div>
      <div class="contact__phone">021583917
        <svg viewBox="0 0 24 24" aria-hidden="true"><path d="M6.6 10.8a15.1 15.1 0 0 0 6.6 6.6l2.2-2.2a1 1 0 0 1 1-.25 11.4 11.4 0 0 0 3.6.57 1 1 0 0 1 1 1V20a1 1 0 0 1-1 1A17 17 0 0 1 3 4a1 1 0 0 1 1-1h3.5a1 1 0 0 1 1 1c0 1.25.2 2.45.57 3.6a1 1 0 0 1-.25 1z"/></svg>
      </div>
    </div>
    <div class="wordmark"><span class="wordmark__square"></span>Tidewood Builders</div>
  </section>
</main>
</body>
</html>
```